Prime Global Casting Agency Needs creative business card design

We manage actors careers and book them liaising and promoting their profiles internationally through Casting Directors, Producers, Directors, Publicists etc. We need clearly visable contact details but with a design that reflects our status and creativity of TV, Feature Film industry. Our logo is attached and needs to relate and our website is www.brisklanestagefolk.com
No flame designs please but please incorporate logo colours.

Target Market(s)

Clients

Industry/Entity Type

Film Production

Contact Information for Business Card

Director Danielle Prowse
Suite F, Building 4, Wrenlow Studios Australia, Kelby Vale, Sydney, NSW 2048

Font styles to use
Sans Serif

Colors
ec1f27

Requirements
Nice to have
• Colours should relate to logo attached and type can relate again to type in the logo design.
Should not have
• No Flames designs and best to be not too obvious with the film designs eiither. Needs to be more creative and modern

```html
<!DOCTYPE html>
<html lang="en">
<head>
<meta charset="utf-8">
<title>Brisklane Stagefolk – Business Card</title>
<link href="https://fonts.googleapis.com/css2?family=Raleway:wght@400;500;600&display=swap" rel="stylesheet">
<style>
  :root {
    --stage: #161617;
    --card: #2e2f33;
    --card-edge: #3a3b40;
    --brand-red: #ec1f27;
    --text-light: #e6e6e8;
    --text-soft: #c9c9cc;
  }
  * { box-sizing: border-box; margin: 0; padding: 0; }
  html, body {
    width: 1200px;
    height: 900px;
    overflow: hidden;
    background: var(--stage);
    font-family: "Raleway", sans-serif;
  }
  .canvas {
    position: relative;
    width: 1200px;
    height: 900px;
  }
  .card {
    position: absolute;
    left: 330px;
    width: 550px;
    height: 318px;
    background: var(--card);
    border: 1px solid var(--card-edge);
    border-radius: 16px;
  }
  .card--front { top: 118px; }
  .card--back { top: 488px; }

  .wordmark {
    position: absolute;
    font-weight: 600;
    letter-spacing: 0.5px;
    white-space: nowrap;
  }
  .card--front .wordmark {
    left: 70px;
    top: 80px;
    font-size: 30px;
    color: var(--brand-red);
  }
  .card--back .wordmark {
    left: 0;
    right: 0;
    top: 128px;
    text-align: center;
    font-size: 36px;
    color: var(--text-light);
  }

  .contact {
    position: absolute;
    left: 254px;
    top: 140px;
  }
  .contact__name {
    font-size: 26px;
    font-weight: 400;
    color: var(--brand-red);
    line-height: 1.1;
  }
  .contact__role {
    font-size: 17px;
    color: var(--text-soft);
    margin-top: 2px;
  }
  .contact__lines {
    list-style: none;
    margin-top: 22px;
    margin-left: 4px;
    font-size: 15px;
    line-height: 19px;
    color: var(--text-light);
  }
</style>
</head>
<body>
  <main class="canvas">
    <section class="card card--front" aria-label="Card front">
      <div class="wordmark">Brisklane Stagefolk</div>
      <div class="contact">
        <p class="contact__name">Marcus Ellery</p>
        <p class="contact__role">Managing Director</p>
        <ul class="contact__lines">
          <li>info@brisklanestagefolk.com</li>
          <li>044-987 654 321</li>
        </ul>
      </div>
    </section>

    <section class="card card--back" aria-label="Card back">
      <div class="wordmark">Brisklane Stagefolk</div>
    </section>
  </main>
</body>
</html>
```